Web Developer Needs a Business Card Design

I need a personal business card design that represents me as a web developer for potential employers. I would like the background to be a dark color on the front for contrast with my logo and name. The back will have all my information along with a smaller version of the logo. I want something with a modern look and feel, not too conservative. This will be used for potential employers and freelance work.

Industry/Entity Type

Business

Contact Information for Business Card

Front should have my logo and name. The back should have all my personal information which would include: name: Tom Varulek, phone: 570-614-3098, email: tomvarulek@quillbox.net, website url: www.tomvarulek.net, logo, web developer.

Font styles to use
Sans Serif

Requirements
Must have
• Must include my logo. The color palette base color will be the logo color.

```html
<!DOCTYPE html>
<html lang="en">
<head>
<meta charset="utf-8">
<title>Tom Varulek – Business Card</title>
<link href="https://fonts.googleapis.com/css2?family=Questrial&display=swap" rel="stylesheet">
<style>
  :root {
    --backdrop: #8b8c8c;
    --ink-dark: #231e1d;
    --pattern-tone: #2c302c;
    --teal: #4cc9a8;
    --paper: #e6e6e6;
    --text-grey: #6d6d6d;
    --text-body: #3a3a3a;
    --edge: #151111;
  }
  * { box-sizing: border-box; margin: 0; padding: 0; }
  html, body {
    width: 1200px;
    height: 900px;
    overflow: hidden;
    background: var(--backdrop);
    font-family: "Questrial", "Century Gothic", sans-serif;
  }
  .stage {
    position: relative;
    width: 1200px;
    height: 900px;
  }
  .card {
    position: absolute;
    left: 300px;
    width: 600px;
    height: 343px;
    overflow: hidden;
  }
  .card--front { top: 77px; background: var(--ink-dark); }
  .card--back  { top: 480px; background: var(--paper); }

  /* front */
  .front-pattern {
    position: absolute;
    inset: 0;
    background: radial-gradient(ellipse at center, var(--pattern-tone) 0%, var(--ink-dark) 85%);
  }
  .front-mark {
    position: absolute;
    inset: 0;
    display: flex;
    align-items: center;
    justify-content: center;
    gap: 14px;
  }
  .mark-dot {
    width: 22px;
    height: 22px;
    border-radius: 50%;
    background: var(--teal);
  }
  .mark-name {
    color: var(--teal);
    font-size: 34px;
    letter-spacing: 0.5px;
  }

  /* back */
  .back-shape {
    position: absolute;
    inset: 0;
  }
  .back-mark {
    position: absolute;
    left: 330px;
    top: 0;
    width: 270px;
    height: 343px;
    display: flex;
    align-items: center;
    justify-content: center;
    color: var(--teal);
    font-size: 28px;
  }
  .identity {
    position: absolute;
    left: 38px;
    top: 42px;
  }
  .identity-name {
    color: var(--teal);
    font-size: 29px;
    font-weight: 400;
    letter-spacing: 0.3px;
  }
  .identity-role {
    margin-top: 6px;
    color: var(--text-grey);
    font-size: 17px;
  }
  .contact-list {
    position: absolute;
    left: 43px;
    top: 160px;
    list-style: none;
  }
  .contact-item {
    display: flex;
    align-items: center;
    height: 25px;
    color: var(--text-body);
    font-size: 15.5px;
  }
  .contact-icon {
    width: 16px;
    height: 16px;
    margin-right: 15px;
    flex: none;
  }
  .contact-dot {
    width: 14px;
    height: 14px;
    margin: 0 16px 0 1px;
    border-radius: 50%;
    background: var(--teal);
    flex: none;
  }
</style>
</head>
<body>
<main class="stage">

  <section class="card card--front" aria-label="Card front">
    <div class="front-pattern" role="img" aria-label="Faint repeating monogram pattern on dark background"></div>
    <div class="front-mark">
      <span class="mark-dot"></span>
      <span class="mark-name">Tom Varulek</span>
    </div>
  </section>

  <section class="card card--back" aria-label="Card back">
    <svg class="back-shape" width="600" height="343" viewBox="0 0 600 343" aria-hidden="true">
      <circle cx="462" cy="171" r="182" fill="var(--teal)" stroke="var(--edge)" stroke-width="4"/>
      <circle cx="474" cy="171" r="176" fill="var(--ink-dark)"/>
    </svg>
    <div class="back-mark">Tom Varulek</div>

    <header class="identity">
      <h1 class="identity-name">Tom Varulek</h1>
      <p class="identity-role">Front-End Developer</p>
    </header>

    <ul class="contact-list">
      <li class="contact-item">
        <svg class="contact-icon" viewBox="0 0 16 16" aria-hidden="true">
          <path d="M3.2 1.5l2.6 0.2 1.2 3.2-1.7 1.3c0.8 1.8 2.2 3.2 4 4l1.3-1.7 3.2 1.2 0.2 2.6c-0.6 1.6-2.4 2.2-4 1.6C6.3 12.5 3.5 9.7 2 6c-0.6-1.6 0-3.6 1.2-4.5z" fill="var(--teal)"/>
        </svg>
        570-614-3098
      </li>
      <li class="contact-item">
        <svg class="contact-icon" viewBox="0 0 16 16" aria-hidden="true">
          <rect x="1.5" y="3.5" width="13" height="9" fill="var(--teal)"/>
          <path d="M1.5 3.5l6.5 5 6.5-5" fill="none" stroke="var(--paper)" stroke-width="1.3"/>
        </svg>
        tomvarulek@quillbox.net
      </li>
      <li class="contact-item">
        <svg class="contact-icon" viewBox="0 0 16 16" aria-hidden="true">
          <circle cx="8" cy="8" r="6.5" fill="var(--teal)"/>
          <ellipse cx="8" cy="8" rx="2.8" ry="6.5" fill="none" stroke="var(--paper)" stroke-width="1"/>
          <path d="M1.5 8h13" stroke="var(--paper)" stroke-width="1"/>
        </svg>
        www.tomvarulek.net
      </li>
      <li class="contact-item"><span class="contact-dot"></span>@tomvarulek</li>
      <li class="contact-item"><span class="contact-dot"></span>tomvarulek.net/profile</li>
      <li class="contact-item"><span class="contact-dot"></span>tomvarulek.net/code</li>
    </ul>
  </section>

</main>
</body>
</html>
```